Design for the A4 Letterhead, envelope and A4 Folder

Design have to be clean, professional, unique (eye catchy) and high end.
Colors: Yellow (Code: 803C), Darker Grey and Black or white (optional)
Logo can be in white or black

Letterhead:
Contain: 1. Korvane Logo
2. Slogan "MADE WITH PRIDE"
3. Company information:
Korvane Valves Pte. Ltd. (Singapore)
Registration no: 201947215K
Tel: (65) 6418 2904
Fax: (65) 6472 9186
Email: sales@korvanevalves.example
Website: http://www.korvanevalves.example
4. Logo watermark

Envelope:
Contain: 1. Korvane Logo
3. website: http://www.korvanevalves.example and email address:
sales@korvanevalves.example
4. Logo watermark

Folder:
Contain: 1. Korvane Logo
3. Company's information:
Tel: (65) 6418 2904
Fax: (65) 6472 9186
4. QR Code
5. Logo watermark
6. On the inside there is a space to insert business card. Contrast colors
between the inside and cover.
Updates

For the Folder design, please be informed that we would prefer to have the Korvane logo on the left hand side of the cover page, rather than on the right hand side.And also if we could highlight the "Made with Pride" slogan with either the yellow box or black/grey box depending on the background color.For the Envelope design,it does not matter where the position of the logo is. But please also highlight the "Made with Pride" Slogan For the Letterhead design, the position of the logo must be on the left hand side and the slogan must be highlighted. In addition, please include the following company information (only for the letterhead design)Korvane Valves Pte. Ltd. (Singapore)Registration no: 200308878MTel: (65) 6535 3735Fax: (65) 6533 3570Email: sales@dynatechpumps.comWebsite: http://www.korvanevalves.example Added Wednesday, August 2, 2017

Target Market(s)

Business to Business, High End market

Industry/Entity Type

It Professional

Font styles to use
Serif

Requirements
Must have
• Design have to be clean, professional, unique (eye catchy) and high end.
Nice to have
• color contrast but still maintaining the professionalism and the seriousness
Should not have
• Messy look, futuristic look, too crowded

```html
<!DOCTYPE html>
<html lang="en">
<head>
<meta charset="utf-8">
<title>Korvane Valves – Letterhead</title>
<link rel="stylesheet" href="https://fonts.googleapis.com/css2?family=Noto+Serif:wght@700&family=Open+Sans:wght@400;700&display=swap">
<style>
  :root {
    --brand-yellow: #ffe900;
    --brand-yellow-soft: #fff36b;
    --steel-grey: #9a9a9a;
    --steel-light: #d9d9d9;
    --ink: #1a1a1a;
    --text-grey: #555555;
    --paper: #ffffff;
    --backdrop: #e9e1a0;
    --watermark: #efefef;
  }
  * { box-sizing: border-box; margin: 0; padding: 0; }
  html, body { width: 1200px; height: 784px; overflow: hidden; }
  body {
    background: var(--backdrop);
    display: flex;
    align-items: center;
    justify-content: center;
    font-family: "Open Sans", Arial, sans-serif;
  }
  .letterhead {
    position: relative;
    width: 520px;
    height: 735px;
    background: var(--paper);
    box-shadow: 0 4px 18px rgba(0,0,0,0.12);
    overflow: hidden;
  }
  .corner-tab { position: absolute; top: 0; height: 5px; }
  .corner-tab--grey-left { left: 0; width: 40px; background: var(--steel-grey); }
  .corner-tab--yellow-right { right: 0; width: 40px; background: var(--brand-yellow); }
  .corner-tab--grey-right { right: 40px; width: 28px; background: var(--steel-light); }

  .brand {
    position: absolute;
    top: 26px;
    left: 30px;
    display: flex;
    align-items: center;
    gap: 8px;
  }
  .brand__dot {
    width: 22px; height: 22px;
    border-radius: 50%;
    background: var(--ink);
  }
  .brand__name {
    font-family: "Open Sans", Arial, sans-serif;
    font-weight: 700;
    font-size: 20px;
    letter-spacing: 1px;
    color: var(--ink);
  }

  .company-info {
    position: absolute;
    top: 26px;
    right: 26px;
    font-size: 8.5px;
    line-height: 1.45;
    color: var(--text-grey);
  }
  .company-info__name { font-weight: 700; color: var(--ink); font-size: 9px; }
  .company-info__row { display: flex; align-items: center; gap: 5px; }
  .company-info__icon {
    width: 6px; height: 6px; border-radius: 50%;
    background: var(--text-grey); flex: none;
  }

  .watermark {
    position: absolute;
    left: 215px;
    top: 590px;
    font-family: "Open Sans", Arial, sans-serif;
    font-weight: 700;
    font-size: 44px;
    color: var(--watermark);
    letter-spacing: 2px;
  }

  .footer-swoosh { position: absolute; left: 0; bottom: 0; width: 520px; height: 120px; }

  .slogan {
    position: absolute;
    left: 58px;
    bottom: 14px;
    font-family: "Noto Serif", Georgia, serif;
    font-weight: 700;
    font-size: 14px;
    letter-spacing: 0.5px;
    color: var(--ink);
  }
</style>
</head>
<body>
  <main class="letterhead">
    <span class="corner-tab corner-tab--grey-left"></span>
    <span class="corner-tab corner-tab--grey-right"></span>
    <span class="corner-tab corner-tab--yellow-right"></span>

    <header class="brand">
      <span class="brand__dot"></span>
      <span class="brand__name">KORVANE</span>
    </header>

    <address class="company-info" style="font-style:normal">
      <div class="company-info__name">Korvane Valves Pte. Ltd. (Singapore)</div>
      <div class="company-info__row"><span class="company-info__icon"></span>Regd. No. 201947215K</div>
      <div class="company-info__row"><span class="company-info__icon"></span>(65) 6418 2904</div>
      <div class="company-info__row"><span class="company-info__icon"></span>(65) 6472 9186</div>
      <div class="company-info__row"><span class="company-info__icon"></span>sales@korvanevalves.example</div>
      <div class="company-info__row"><span class="company-info__icon"></span>www.korvanevalves.example</div>
    </address>

    <div class="watermark" aria-hidden="true">KORVANE</div>

    <svg class="footer-swoosh" viewBox="0 0 520 120" aria-hidden="true">
      <defs>
        <linearGradient id="steelBand" x1="0" y1="0" x2="1" y2="0">
          <stop offset="0" stop-color="#c9c9c9"/>
          <stop offset="0.6" stop-color="#8f8f8f"/>
          <stop offset="1" stop-color="#bdbdbd"/>
        </linearGradient>
        <linearGradient id="yellowBand" x1="0" y1="0" x2="0" y2="1">
          <stop offset="0" stop-color="#fff36b"/>
          <stop offset="1" stop-color="#ffe900"/>
        </linearGradient>
      </defs>
      <path d="M0 40 C120 50 220 70 300 95 C360 112 430 120 520 118 L520 120 L0 120 Z" fill="url(#steelBand)"/>
      <path d="M0 52 C120 60 220 80 300 102 C360 116 430 120 520 120 L0 120 Z" fill="url(#yellowBand)"/>
    </svg>

    <div class="slogan">MADE WITH PRIDE</div>
  </main>
</body>
</html>
```